Brenford SMHO Covid-19 Vaccine Advertisement (Digital + Print)

The client is needing an advertisement that will run during Football and Soccer Season to advertise getting vaccinated for the Covid-19 Shot.
Request - Sports theme related, Scoreboard, Teams match up, covid-19 vs texas theme

Client - Brenford Parish Senior and Mobility Help Office

Various Ad types:
Digital Marketing Insertion Orders
- Door Hanger
- Front Page Note
- Insert Schedule

Print + Digital Insertion Orders
- Print Ads
- Email Marketing
- Banner Ads

Must include: logo and brand colors and 1-888-555-0147, and #ArmReadyNowOK and needs to be an English version and a Spanish Version

Message Ideas to incorporate - a variation - do not use all in one ad
Brenford vs COVID
Let’s win this together!
#VaccineSavesLives
#CancelCOVID
#GetVaccinated
#GetBoosted
#GetProtected

```html
<!DOCTYPE html>
<html lang="en">
<head>
<meta charset="utf-8">
<title>Brenford vs COVID – Let's win this together</title>
<link rel="stylesheet" href="https://fonts.googleapis.com/css2?family=Montserrat:ital,wght@0,400;0,600;0,700;0,800;0,900;1,200;1,700;1,800;1,900&display=swap">
<style>
  :root {
    --navy: #17244f;
    --navy-deep: #0d1533;
    --red: #d3222a;
    --green: #6dbd3f;
    --green-dark: #3f8f2a;
    --blue: #3a55a4;
    --white: #ffffff;
    --pitch: #3f8a2e;
    --sky: #2b4a78;
  }
  html, body {
    margin: 0;
    padding: 0;
    overflow: hidden;
    background: #e9ecef;
  }
  .ad {
    position: relative;
    width: 849px;
    height: 1200px;
    overflow: hidden;
    background: var(--white);
    font-family: "Montserrat", Arial, sans-serif;
  }
  .stadium-scene {
    position: absolute;
    left: 0; top: 0;
    width: 849px; height: 1060px;
    background:
      radial-gradient(ellipse at 50% 18%, rgba(255,255,255,0.35), transparent 45%),
      linear-gradient(180deg, #1d3458 0%, var(--sky) 28%, #5c6f86 48%, #4f7f3c 62%, var(--pitch) 78%, #2f6d25 100%);
  }
  .scoreboard {
    position: absolute;
    left: 0; top: 0;
    width: 849px; height: 360px;
  }
  .hashtag-banner {
    position: absolute;
    left: 255px; top: 112px;
    width: 339px; height: 36px;
    background: var(--red);
    color: var(--white);
    font-weight: 800;
    font-style: italic;
    font-size: 25px;
    line-height: 36px;
    text-align: center;
  }
  .score {
    position: absolute;
    left: 330px; top: 170px;
    width: 190px; height: 34px;
    display: flex;
    background: var(--white);
    color: var(--navy);
    font-weight: 700;
    font-size: 20px;
    line-height: 34px;
    text-align: center;
  }
  .score span { flex: 1; }
  .score .clock { flex: 2; background: var(--navy-deep); color: var(--white); }
  .team {
    position: absolute;
    top: 212px;
    width: 300px;
    text-align: center;
    color: var(--white);
    font-weight: 800;
    font-size: 52px;
    line-height: 1;
  }
  .team-home { left: 100px; }
  .team-away { left: 450px; }
  .shield-icon {
    position: absolute;
    left: 545px; top: 290px;
    width: 150px; height: 170px;
  }
  .versus {
    position: absolute;
    left: 330px; top: 360px;
    color: rgba(255,255,255,0.85);
    font-weight: 900;
    font-style: italic;
    font-size: 140px;
    line-height: 1;
    letter-spacing: -4px;
  }
  .rally {
    position: absolute;
    left: 505px; top: 570px;
    margin: 0;
    color: var(--white);
    font-weight: 800;
    font-style: italic;
    font-size: 86px;
    line-height: 88px;
    text-shadow: 0 3px 10px rgba(0,0,0,0.35);
  }
  .together {
    position: absolute;
    left: 80px; top: 868px;
    width: 700px;
    margin: 0;
    color: var(--white);
    font-weight: 200;
    font-style: italic;
    font-size: 96px;
    line-height: 1;
    letter-spacing: -2px;
    white-space: nowrap;
  }
  .footer-wave {
    position: absolute;
    left: 0; top: 1010px;
    width: 849px; height: 190px;
  }
  .tagline {
    position: absolute;
    left: 28px; top: 1058px;
    color: var(--green);
    font-weight: 800;
    font-style: italic;
    font-size: 36px;
    line-height: 1;
  }
  .phone {
    position: absolute;
    left: 28px; top: 1102px;
    color: var(--blue);
    font-weight: 800;
    font-style: italic;
    font-size: 54px;
    line-height: 1;
  }
  .org-name {
    position: absolute;
    right: 30px; top: 1062px;
    width: 270px;
    display: flex;
    align-items: center;
    gap: 14px;
    color: var(--blue);
    font-weight: 700;
    font-size: 19px;
    line-height: 23px;
    text-transform: uppercase;
  }
  .org-name .dot {
    flex: 0 0 44px;
    height: 44px;
    border-radius: 50%;
    background: var(--green);
  }
</style>
</head>
<body>
<main class="ad">
  <div class="stadium-scene" role="img" aria-label="Floodlit stadium with a footballer in red kicking a virus-shaped ball"></div>

  <svg class="scoreboard" viewBox="0 0 849 360" aria-hidden="true">
    <path d="M60 150 L789 150 L760 300 L89 300 Z" fill="var(--navy)" opacity="0.92"/>
    <path d="M60 150 L789 150" stroke="var(--white)" stroke-width="3" opacity="0.6"/>
  </svg>

  <div class="hashtag-banner">#ArmReadyNowOK</div>
  <div class="score"><span>3</span><span class="clock">90:00</span><span>0</span></div>

  <div class="team team-home">Brenford</div>
  <div class="team team-away">COVID</div>

  <svg class="shield-icon" viewBox="0 0 150 170" aria-hidden="true">
    <path d="M75 4 L142 26 L142 80 C142 125 110 152 75 166 C40 152 8 125 8 80 L8 26 Z" fill="var(--white)"/>
    <path d="M75 16 L130 34 L130 80 C130 118 104 141 75 153 C46 141 20 118 20 80 L20 34 Z" fill="var(--green)"/>
    <path d="M63 52 H87 V74 H109 V98 H87 V120 H63 V98 H41 V74 H63 Z" fill="var(--white)"/>
  </svg>

  <div class="versus">VS</div>

  <p class="rally">Let’s<br>win<br>this</p>
  <p class="together">TOGETHER!</p>

  <svg class="footer-wave" viewBox="0 0 849 190" preserveAspectRatio="none" aria-hidden="true">
    <path d="M0 34 Q424 -6 849 34 L849 190 L0 190 Z" fill="var(--white)"/>
    <path d="M0 30 Q424 -10 849 30" fill="none" stroke="var(--green)" stroke-width="5"/>
  </svg>

  <div class="tagline">#GetBoosted</div>
  <div class="phone">1-888-555-0147</div>

  <div class="org-name"><span class="dot"></span><span>Brenford Parish Senior and Mobility Help Office</span></div>
</main>
</body>
</html>
```